VFX Company Business Card Design Project

The Kestrel Works is a decentralized Visual Effects Studio servicing the television and feature film industries.
Project Brief:
Take our logo that was previously designed on Pencil Harbor and make a double sided business card.
Requirements:
- Card MUST be double sided.
- Front of card MUST have the yellow part of our logo against the dark grey background.
- Back of card is completely up to the designer.
- Back of card must include the complete company logo.
Please follow these File Preparation guidelines:
http://printnook.ca/infopage?file=filetype_en&s=PrintNook_new&lang=en
Business

```html
<!DOCTYPE html>
<html lang="en">
<head>
<meta charset="utf-8">
<title>The Kestrel Works — Business Card</title>
<link href="https://fonts.googleapis.com/css2?family=Mulish:wght@400;500;700&display=swap" rel="stylesheet">
<style>
  :root {
    --stage: #3b3b3b;
    --card: #262626;
    --yellow: #fdc82f;
    --text: #f2f2f2;
  }
  * { box-sizing: border-box; margin: 0; padding: 0; }
  html, body { width: 1200px; height: 900px; overflow: hidden; }
  body {
    background: var(--stage);
    font-family: "Mulish", "Helvetica Neue", Arial, sans-serif;
    position: relative;
  }
  .card {
    position: absolute;
    top: 293px;
    width: 514px;
    height: 314px;
    background: var(--card);
    box-shadow: 0 4px 14px rgba(0,0,0,0.45);
  }
  .card--front { left: 73px; }
  .card--back { left: 615px; }

  .front-name {
    position: absolute;
    left: 100px;
    bottom: 40px;
    color: var(--yellow);
    font-weight: 700;
    font-size: 40px;
    line-height: 1.05;
    letter-spacing: 0.5px;
  }

  .brand {
    position: absolute;
    left: 30px;
    top: 150px;
    width: 200px;
    display: flex;
    align-items: center;
    gap: 10px;
    justify-content: center;
  }
  .brand__dot {
    width: 14px; height: 14px;
    border-radius: 50%;
    background: var(--yellow);
    flex: none;
  }
  .brand__name {
    color: var(--text);
    font-weight: 700;
    font-size: 20px;
    white-space: nowrap;
  }

  .divider {
    position: absolute;
    left: 257px;
    top: 57px;
    width: 2px;
    height: 200px;
    background: var(--yellow);
  }

  .contact {
    position: absolute;
    left: 284px;
    top: 58px;
    color: var(--text);
  }
  .contact__name {
    color: var(--yellow);
    font-size: 22px;
    font-weight: 500;
    line-height: 1.1;
  }
  .contact__role {
    font-size: 15px;
    margin-top: 3px;
  }
  .contact__group { margin-top: 20px; }
  .contact__line {
    display: flex;
    align-items: flex-start;
    gap: 6px;
    font-size: 13px;
    line-height: 16px;
  }
  .contact__line svg { flex: none; margin-top: 2px; fill: var(--yellow); }
  .contact__line span { display: block; }
</style>
</head>
<body>
  <section class="card card--front">
    <p class="front-name">The Kestrel<br>Works</p>
  </section>

  <section class="card card--back">
    <div class="brand">
      <span class="brand__dot"></span>
      <span class="brand__name">The Kestrel Works</span>
    </div>

    <div class="divider"></div>

    <div class="contact">
      <h1 class="contact__name">Martin Okafor</h1>
      <p class="contact__role">managing director</p>

      <div class="contact__group">
        <div class="contact__line">
          <svg width="10" height="12" viewBox="0 0 10 12"><path d="M5 0a4.5 4.5 0 0 0-4.5 4.5C.5 8 5 12 5 12s4.5-4 4.5-7.5A4.5 4.5 0 0 0 5 0zm0 6.3a1.8 1.8 0 1 1 0-3.6 1.8 1.8 0 0 1 0 3.6z"/></svg>
          <div><span>48 Harbor Lane</span><span>Millbrook, New York 12545</span></div>
        </div>
      </div>

      <div class="contact__group">
        <div class="contact__line">
          <svg width="10" height="12" viewBox="0 0 10 12"><path d="M2 0h6a1 1 0 0 1 1 1v10a1 1 0 0 1-1 1H2a1 1 0 0 1-1-1V1a1 1 0 0 1 1-1zm.5 1.5v7.5h5V1.5z"/></svg>
          <span>212 406 31 78</span>
        </div>
        <div class="contact__line">
          <svg width="10" height="12" viewBox="0 0 10 12"><path d="M2.5 1h5v3h-5zM0 4.5h10V9H8v2H2V9H0zm3 4v1.8h4V8.5z"/></svg>
          <span>212 406 31 79</span>
        </div>
      </div>

      <div class="contact__group">
        <div class="contact__line">
          <svg width="10" height="12" viewBox="0 0 10 12"><path d="M0 3h10v6H0zm1 1l4 3 4-3z"/></svg>
          <span>info@kestrelworks.com</span>
        </div>
        <div class="contact__line">
          <svg width="10" height="12" viewBox="0 0 10 12"><path d="M5 1a5 5 0 1 0 0 10A5 5 0 0 0 5 1zm0 1c.6.6 1 1.6 1.2 2.5H3.8C4 3.6 4.4 2.6 5 2zM1.2 5.5h1.6c0 .4 0 .7.1 1H1.2a4 4 0 0 1 0-1zm2.6 0h2.4v1H3.8zm3.4 0h1.6a4 4 0 0 1 0 1H7.2zM3.8 7.5h2.4C6 8.4 5.6 9.4 5 10c-.6-.6-1-1.6-1.2-2.5z"/></svg>
          <span>www.kestrelworks.com</span>
        </div>
      </div>
    </div>
  </section>
</body>
</html>
```